Kestrel Facilities Business Card Design

We would now like to design business cards with the new Kestrel Facilities logo

Target Market(s)

Professional

Industry/Entity Type

Professional services

Contact Information for Business Card

Employee name, title, phone number, email address, corporate office address and logo.

Font styles to use
Sans Serif

Colors
0054AA
0677BA
7BADD7
CADEEF
E8F1F8

Requirements
Must have
• My logo
Should not have
• any other pictures or images besides my logo

```html
<!DOCTYPE html>
<html lang="en">
<head>
<meta charset="utf-8">
<title>Kestrel Facilities Business Card</title>
<link href="https://fonts.googleapis.com/css2?family=Montserrat:wght@400;500;700&display=swap" rel="stylesheet">
<style>
  :root {
    --page-bg: #121212;
    --card-bg: #1f1f1f;
    --card-back-bg: #1a1a1a;
    --pattern-a: #2a2a2a;
    --pattern-b: #333333;
    --brand-blue: #3585cf;
    --rule-blue: #2f7fca;
    --text-light: #f2f2f2;
  }
  * { box-sizing: border-box; margin: 0; padding: 0; }
  html, body {
    width: 1200px; height: 900px; overflow: hidden;
    background: var(--page-bg);
    font-family: "Montserrat", sans-serif;
  }
  .canvas { position: relative; width: 1200px; height: 900px; }
  .card {
    position: absolute; left: 290px; width: 620px; height: 354px;
    box-shadow: 0 18px 40px rgba(0,0,0,0.6);
  }
  .card-back { top: 50px; background: var(--card-back-bg); }
  .card-front { top: 470px; background: var(--card-bg); }

  .monogram-pattern {
    position: absolute; inset: 0;
    background: linear-gradient(135deg, var(--pattern-b), var(--pattern-a));
  }
  .back-wordmark {
    position: absolute; top: 50%; left: 50%; transform: translate(-50%, -50%);
    display: flex; align-items: center; gap: 10px;
    padding: 12px 18px; background: var(--card-back-bg);
    color: var(--brand-blue); font-weight: 700; font-size: 20px; white-space: nowrap;
  }
  .mark-square { width: 18px; height: 18px; background: var(--brand-blue); }

  .front-wordmark {
    position: absolute; top: 52px; right: 44px;
    display: flex; align-items: center; gap: 12px;
    color: var(--brand-blue); font-weight: 700; font-size: 30px; white-space: nowrap;
  }
  .front-wordmark .mark-square { width: 30px; height: 30px; }

  .person { position: absolute; left: 44px; top: 168px; }
  .person-name { color: var(--brand-blue); font-weight: 700; font-size: 22px; }
  .person-title { color: var(--text-light); font-size: 15px; margin-top: 2px; }

  .divider {
    position: absolute; left: 44px; right: 44px; top: 232px;
    height: 2px; background: var(--rule-blue);
  }
  .contact { position: absolute; left: 44px; top: 250px; list-style: none; }
  .contact li {
    display: flex; align-items: center; gap: 10px;
    color: var(--text-light); font-size: 16px; line-height: 26px;
  }
  .contact svg { width: 14px; height: 14px; }
  .address {
    position: absolute; right: 44px; bottom: 28px; text-align: right;
    color: var(--text-light); font-size: 16px; line-height: 24px;
  }
</style>
</head>
<body>
<main class="canvas">
  <section class="card card-back">
    <div class="monogram-pattern" role="img" aria-label="Repeating monogram pattern in dark grey tones"></div>
    <div class="back-wordmark"><span class="mark-square"></span>Kestrel Facilities</div>
  </section>

  <section class="card card-front">
    <div class="front-wordmark"><span class="mark-square"></span>Kestrel Facilities</div>

    <div class="person">
      <p class="person-name">Daniel Hartley</p>
      <p class="person-title">Director</p>
    </div>

    <div class="divider"></div>

    <ul class="contact">
      <li>
        <svg viewBox="0 0 24 24" fill="none" stroke="#3585cf" stroke-width="2.2" aria-hidden="true"><path d="M6 3l3 1 1 4-2 2c1 3 3 5 6 6l2-2 4 1 1 3-2 3C10 21 3 14 3 6z"/></svg>
        (555) 204-3187
      </li>
      <li>
        <svg viewBox="0 0 24 24" fill="none" stroke="#3585cf" stroke-width="2.2" aria-hidden="true"><rect x="3" y="5" width="18" height="14"/><path d="M3 5l9 8 9-8"/></svg>
        info@kestrelfacilities.com
      </li>
    </ul>

    <address class="address">
      1187 Cedar Ridge Lane<br>
      Millbrook, OR 97000
    </address>
  </section>
</main>
</body>
</html>
```